Meridian Tidewren Pale Ale Beer Label/Badge

We need a Beer Label designed for our first official beer to be launched under The meridian Brand!!
It will be a Pale Ale Called "Tidewren Pale Ale"!

The Meridian has the largest Craft Beer & Cider selection in the Geelong & Surf Coast region. With a funky location and a relaxed vibe, Meridian prides itself on serving delicious, unique seasonal food paired with Australia's best Craft Beer. The meridian is the perfect setting for a relaxed afternoon or evening with friends and can package an experience for larger groups or corporate bookings.

The Meridian Tavern brand has been growing for over a year and a half and the first label needs to integrate The meridian Logo but at the same time bring a fresh, new and eye catching feel to it along with embracing the "Odysseus" story in which we will be naming future beers.

The story of Tidewren is found via the following link
http://lorevault.example/wiki/Tidewren_(folklore)

We expect designers to research The meridian Tavern brand along with the all important Craft Beer Market and demographics. This will, potentially, be the start of many more labels to come for the winning designer!!

Requirements
Must have
• The original "O" needs to be integrated into the new logo and as much as the Greek mythology is being used it needs to be certain that this is an original Australian Craft Beer in the modern age!!
strong, modern & unique!!
Nice to have
• Logo could have a depiction of Tidewren
Should not have
• tackiness or cheap!!

```html
<!DOCTYPE html>
<html lang="en">
<head>
<meta charset="utf-8">
<title>Meridian Tidewren Pale Ale Label</title>
<link rel="stylesheet" href="https://fonts.googleapis.com/css2?family=Josefin+Sans:wght@300;400;700&display=swap">
<style>
  :root {
    --paper: #ffffff;
    --bark: #5a4a3c;
    --sand: #a8916f;
    --cream: #fbf7ef;
    --rose: #d8737c;
  }
  html, body {
    margin: 0;
    padding: 0;
    width: 748px;
    height: 1200px;
    overflow: hidden;
    background: var(--paper);
  }
  .canvas {
    position: relative;
    width: 748px;
    height: 1200px;
    background: var(--paper);
  }
  .label {
    position: absolute;
    left: 98px;
    top: 128px;
    width: 552px;
    height: 967px;
    background: var(--bark);
    overflow: hidden;
  }
  .label-shapes {
    position: absolute;
    inset: 0;
    width: 552px;
    height: 967px;
  }
  .brand-name,
  .brand-sub,
  .beer-name,
  .beer-style {
    position: absolute;
    left: 0;
    width: 100%;
    margin: 0;
    text-align: center;
    text-transform: uppercase;
    line-height: 1;
    font-family: "Josefin Sans", sans-serif;
    white-space: nowrap;
  }
  .brand-name {
    top: 32px;
    font-size: 66px;
    font-weight: 700;
    letter-spacing: 7px;
    color: var(--cream);
  }
  .brand-sub {
    top: 110px;
    font-size: 20px;
    font-weight: 400;
    letter-spacing: 8px;
    color: var(--cream);
  }
  .brand-seal {
    position: absolute;
    left: 221px;
    top: 180px;
    width: 110px;
    height: 110px;
    border-radius: 50%;
    background: var(--bark);
  }
  .tidewren-figure {
    position: absolute;
    left: 188px;
    top: 395px;
    width: 176px;
    height: 245px;
    border-radius: 88px 88px 10px 10px;
    background: radial-gradient(ellipse at 50% 40%, #ffffff 0%, #f1ebe0 70%, #e3d9c8 100%);
  }
  .beer-name {
    top: 668px;
    font-size: 78px;
    font-weight: 700;
    letter-spacing: 3px;
    color: var(--cream);
  }
  .beer-style {
    top: 800px;
    font-size: 72px;
    font-weight: 300;
    letter-spacing: 6px;
    color: var(--rose);
  }
</style>
</head>
<body>
  <main class="canvas">
    <section class="label">
      <svg class="label-shapes" viewBox="0 0 552 967" aria-hidden="true">
        <polygon class="upper-panel" points="0,0 552,0 552,107 276,440 0,107" fill="#a8916f"/>
        <polygon class="lower-panel" points="276,390 552,593 552,775 0,775 0,593" fill="#a8916f"/>
      </svg>

      <h1 class="brand-name">Meridian</h1>
      <p class="brand-sub">Tavern + Brewery</p>
      <div class="brand-seal" aria-hidden="true"></div>

      <div class="tidewren-figure" role="img" aria-label="Placeholder for the Tidewren emblem illustration"></div>

      <h2 class="beer-name">Tidewren</h2>
      <p class="beer-style">Pale Ale</p>
    </section>
  </main>
</body>
</html>
```